VELMOR Website Design

We need a website designed for our company VELMOR. We are a luxury lifestyle club that will provide benefits and services for our members. The site should be clean & sleek, preferably using black and white (or darker colors). (example sites: stravenhall.example, plinth.example)

Here is a link of a sample page I did using wix. (https://dunmere7.sitehostly.example/mysite) This can be used to get a general idea.

Target Market(s)

Upper Middle Class in the United States

Number of Pages Required

5+ page

Font styles to use
Sans Serif
Other font styles liked:
• Arial (or other similar fonts)

Requirements
Must have
• A clean design that is eye-catching and speaks to our company.
Nice to have
• Ideas for copy.

```html
<!DOCTYPE html>
<html lang="en">
<head>
<meta charset="utf-8">
<title>VELMOR — About</title>
<link rel="stylesheet" href="https://fonts.googleapis.com/css2?family=Nunito+Sans:ital,wght@0,200;0,300;0,400;1,300&family=Arimo:ital,wght@0,400;0,700;1,400&display=swap">
<style>
:root{
  --black:#000;
  --white:#fff;
  --ghost:#3f3f3f;
  --mist:#b9b9b9;
  --rule:#cfcfcf;
  --hero-a:#c9b89a;
  --hero-b:#6f9a4a;
  --cabin-a:#d8cfc2;
  --cabin-b:#8d7d6c;
}
*{margin:0;padding:0;box-sizing:border-box}
html,body{width:1077px;height:1200px;overflow:hidden;background:var(--black)}
body{position:relative;font-family:"Nunito Sans",Arial,sans-serif;color:var(--white)}
.topbar{position:absolute;left:0;top:0;width:1077px;height:38px;background:var(--white)}
.brand{position:absolute;left:16px;top:9px;font-size:18px;font-weight:300;color:var(--black);letter-spacing:.5px}
.nav{position:absolute;top:14px;left:0;width:1077px;font-family:Arimo,Arial,sans-serif;font-size:6px;color:#222}
.nav a{position:absolute;color:inherit;text-decoration:none;text-transform:uppercase;white-space:nowrap}
.nav .current{background:var(--black);color:var(--white);padding:2px 5px;top:-2px}
.nav-pointer{position:absolute;left:857px;top:33px;width:0;height:0;border-left:6px solid transparent;border-right:6px solid transparent;border-bottom:5px solid var(--white);z-index:2}
.strip{position:absolute;left:0;top:38px;width:1077px;height:9px;background:var(--black)}
.hero{position:absolute;left:0;top:47px;width:1077px;height:466px;background:linear-gradient(100deg,var(--hero-a) 0%,#b7a588 35%,#3f5a2e 60%,var(--hero-b) 100%)}
.title-band{position:absolute;left:0;top:513px;width:1077px;height:91px;background:var(--black);overflow:hidden}
.title-band .giant{position:absolute;left:252px;top:-10px;width:572px;display:flex;justify-content:space-between;font-size:166px;font-weight:200;color:var(--ghost);line-height:1}
.tagline-band{position:absolute;left:0;top:604px;width:1077px;height:56px;background:var(--white)}
.tagline{position:absolute;left:0;top:11px;width:1077px;text-align:center;font-size:28px;font-style:italic;font-weight:300;color:var(--mist)}
.about{position:absolute;left:0;top:660px;width:1077px;height:428px}
.info-icon{position:absolute;left:41px;top:709px}
.about-copy{position:absolute;left:42px;top:728px;width:322px;text-align:center}
.about-copy h1{font-size:25px;font-weight:400;letter-spacing:.3px;margin-bottom:11px;padding-left:20px}
.about-copy p{font-size:13.4px;font-weight:300;line-height:14px;margin-bottom:14px}
.apply{position:absolute;left:125px;top:1014px;width:158px;height:22px;border:2px solid var(--white);font-family:Arimo,Arial,sans-serif;font-weight:700;font-size:11px;text-align:center;line-height:17px;letter-spacing:.5px}
.cabin{position:absolute;left:436px;top:710px;width:589px;height:322px;background:linear-gradient(115deg,var(--cabin-b) 0%,var(--cabin-a) 45%,#efece7 75%,#c9c1b5 100%)}
.cabin-rule{position:absolute;left:436px;top:1032px;width:589px;height:3px;background:var(--white)}
.quote{position:absolute;left:436px;top:1000px;width:578px;text-align:right;font-family:Arimo,Arial,sans-serif;font-style:italic;font-size:20px;color:var(--white)}
.footer-rule{position:absolute;left:0;top:1088px;width:1077px;height:1px;background:var(--rule)}
.footer{position:absolute;left:0;top:1089px;width:1077px;height:111px;font-family:Arimo,Arial,sans-serif}
.foot-brand{position:absolute;left:174px;top:33px;font-family:"Nunito Sans",Arial,sans-serif;font-size:17px;font-weight:300}
.foot-copy{position:absolute;left:187px;top:68px;font-size:5px}
.foot-links{position:absolute;left:286px;top:33px;font-size:7.5px;line-height:13.3px}
.foot-social{position:absolute;left:398px;top:33px;font-size:7.5px;line-height:13.3px}
.foot-social li{list-style:none;display:flex;align-items:center;gap:12px}
.foot-social .dot{width:5px;height:5px;border-radius:50%;background:var(--white)}
.foot-links li{list-style:none}
.newsletter-label{position:absolute;left:512px;top:34px;font-size:7.5px}
.newsletter{position:absolute;left:512px;top:53px;width:151px;height:22px;border:1px solid var(--white);display:flex}
.newsletter .field{flex:1;font-size:6.5px;padding-left:10px;line-height:20px}
.newsletter .ok{width:33px;background:var(--white);color:var(--black);font-size:5.5px;text-align:center;line-height:20px}
.contact{position:absolute;left:794px;top:34px;font-size:6.5px;line-height:11.3px}
</style>
</head>
<body>
<header class="topbar">
  <div class="brand">VELMOR</div>
  <nav class="nav">
    <a style="left:811px">Home</a>
    <a class="current" style="left:849px">About</a>
    <a style="left:902px">Services &amp; Benefits</a>
    <a style="left:989px">Apply</a>
    <a style="left:1032px">Contact</a>
  </nav>
</header>
<div class="strip"></div>
<div class="nav-pointer"></div>
<div class="hero" role="img" aria-label="Dark convertible luxury car parked before a Mediterranean villa with palm trees and lawn"></div>

<section class="title-band" aria-label="About">
  <div class="giant"><span>A</span><span>B</span><span>O</span><span>U</span><span>T</span></div>
</section>
<section class="tagline-band"><p class="tagline">A Members Only Lifestyle Club</p></section>

<section class="about">
</section>
<svg class="info-icon" width="25" height="25" viewBox="0 0 25 25" aria-hidden="true">
  <circle cx="12.5" cy="12.5" r="11" fill="none" stroke="#fff" stroke-width="2"/>
  <circle cx="12.5" cy="7.5" r="1.6" fill="#fff"/>
  <rect x="11.2" y="10.5" width="2.6" height="8" fill="#fff"/>
</svg>
<div class="about-copy">
  <h1>ABOUT VELMOR</h1>
  <p>VELMOR was formed to bring the best services, experiences, and exclusive opportunities to our members.</p>
  <p>With everything from private member events to private jet travel, the perks of being a VELMOR member are unmatched.</p>
  <p>Professional athletes, artists, musicians, corporate professionals: Our members come from diverse backgrounds.</p>
  <p>Comprehensive services like 24/7 concierge, accountants, attorneys, private advisers, planners, investment advisors and more.</p>
</div>
<div class="apply">APPLY</div>
<div class="cabin" role="img" aria-label="Woman seated in a private jet cabin looking out of the window"></div>
<div class="cabin-rule"></div>
<p class="quote">“The ultimate full service lifestyle club”</p>

<div class="footer-rule"></div>
<footer class="footer">
  <div class="foot-brand">VELMOR</div>
  <div class="foot-copy">© VELMOR 2017</div>
  <ul class="foot-links"><li>About Us</li><li>Contact</li><li>Terms &amp; Conditions</li></ul>
  <ul class="foot-social">
    <li><span class="dot"></span>Circlefeed</li>
    <li><span class="dot"></span>Chirpline</li>
    <li><span class="dot"></span>Snapgrid</li>
  </ul>
  <div class="newsletter-label">Subscribe to our newsletter</div>
  <div class="newsletter"><span class="field">Email Address</span><span class="ok">OK</span></div>
  <address class="contact" style="font-style:normal">18 Larkspur Ave. Fairmont, CA 90000<br>+1 555 010 2040<br>velmorclub@mail.example</address>
</footer>
</body>
</html>
```